Real Estate Business Card

On the front side I want to have my info, my brokerage info.
On the back side I want have my complany’s logo, website and Facebook link. I will provide all this once I select a design.

I would like to see Black background and gold text, Dark Blue and gold text and White and blue text designs

Font styles to use
Sans Serif
Script

```html
<!DOCTYPE html>
<html lang="en">
<head>
<meta charset="utf-8">
<title>Ellery Nest – Business Card</title>
<link rel="stylesheet" href="https://fonts.googleapis.com/css2?family=Cinzel:wght@400;600&family=Open+Sans:wght@400&display=swap">
<style>
  :root {
    --backdrop: #5a5a5a;
    --brand-blue: #2251a8;
    --motif-light: #5a7fc4;
    --blue-top: #2853b2;
    --blue-bottom: #1b3d8a;
    --paper: #ffffff;
    --ink: #3a3a3a;
    --gold: #ecc54c;
    --white-text: #f2f4fa;
  }
  html, body {
    margin: 0;
    width: 1200px;
    height: 802px;
    overflow: hidden;
    background: var(--backdrop);
  }
  .stage { position: relative; width: 1200px; height: 802px; }
  .card {
    position: absolute;
    top: 274px;
    width: 443px;
    height: 265px;
    box-shadow: 2px 3px 6px rgba(0,0,0,0.45);
  }
  .card--front { left: 136px; background: var(--paper); }
  .card--back { left: 624px; }
  .card svg { display: block; width: 100%; height: 100%; }
  .name { font-family: "Cinzel", serif; font-weight: 600; font-size: 22px; fill: var(--brand-blue); }
  .role { font-family: "Open Sans", sans-serif; font-size: 16px; fill: var(--ink); }
  .contact { font-family: "Open Sans", sans-serif; font-size: 16px; fill: var(--ink); }
  .icon { fill: var(--brand-blue); }
  .brand-name { font-family: "Cinzel", serif; font-weight: 600; font-size: 46px; fill: var(--gold); letter-spacing: 1px; }
  .social-link { font-family: "Open Sans", sans-serif; font-size: 16px; fill: var(--white-text); }
</style>
</head>
<body>
<div class="stage">

  <div class="card card--front">
    <svg viewBox="0 0 544 326" xmlns="http://www.w3.org/2000/svg">
      <defs>
        <linearGradient id="motifFill" x1="0" y1="0" x2="1" y2="0">
          <stop offset="0" stop-color="var(--brand-blue)"/>
          <stop offset="1" stop-color="var(--motif-light)"/>
        </linearGradient>
      </defs>
      <rect class="side-band" x="0" y="0" width="118" height="326" fill="var(--brand-blue)"/>
      <rect class="motif-placeholder" x="118" y="90" width="88" height="144"
        fill="url(#motifFill)" role="img" aria-label="Brand motif area"/>

      <text class="name" x="504" y="96" text-anchor="end">Marcus Ellery</text>
      <text class="role" x="503" y="115" text-anchor="end">Managing Director</text>

      <text class="contact" x="491" y="150" text-anchor="end">044-555 210 384</text>
      <text class="contact" x="491" y="169" text-anchor="end">044-555 210 385</text>
      <text class="contact" x="491" y="188" text-anchor="end">044-555 210 386</text>
      <text class="contact" x="491" y="208" text-anchor="end">hello@ellerynest.com</text>
      <text class="contact" x="491" y="227" text-anchor="end">www.ellerynest.com</text>

      <g class="icon">
        <path d="M494 140 h12 l-1 3 h-3 l-1 -1 h-2 l-1 1 h-3 z M496 143 h8 v3 h-8 z"/>
        <rect x="496" y="158" width="7" height="11" rx="1"/>
        <rect x="497.5" y="159.5" width="4" height="7" fill="var(--paper)"/>
        <rect x="497" y="178" width="7" height="3"/>
        <rect x="494" y="181" width="12" height="5" rx="1"/>
        <rect x="497" y="185" width="7" height="3"/>
        <rect x="494" y="198" width="12" height="8"/>
        <path d="M494 198 l6 5 l6 -5" fill="none" stroke="var(--paper)" stroke-width="1.2"/>
        <circle cx="500" cy="222" r="5.5"/>
      </g>

      <text class="contact" x="506" y="257" text-anchor="end">48 Linden Row, Suite 2</text>
      <text class="contact" x="506" y="276" text-anchor="end">Westmoor, 204816</text>
    </svg>
  </div>

  <div class="card card--back">
    <svg viewBox="0 0 545 326" xmlns="http://www.w3.org/2000/svg">
      <defs>
        <linearGradient id="backFill" x1="0" y1="0" x2="0" y2="1">
          <stop offset="0" stop-color="var(--blue-top)"/>
          <stop offset="1" stop-color="var(--blue-bottom)"/>
        </linearGradient>
      </defs>
      <rect x="0" y="0" width="545" height="326" fill="url(#backFill)"/>
      <text class="brand-name" x="272" y="198" text-anchor="middle">Ellery Nest</text>
      <text class="social-link" x="272" y="276" text-anchor="middle">www.linkhub.com/ellerynest</text>
    </svg>
  </div>

</div>
</body>
</html>
```